Rowdy Ledgers (Podcast)

A simple website that allows users to follow and sign up to our podcast.

"Rowdy Ledgers with Tarq and Milo" is a humourous look at economics and entrepreneurship in the world. We interview up and coming fundrocket projects and established entrepreneurs and subject matter experts. It's about practical real life smarts.

We value liberty, intelligence and humour.

The aim of the website is to attract retain and build a list of young people that share our values.

Podcast we enjoy (But not their website as it's to noisy and scattered): http://www.grumblecast.net/

Reason: To allow for sufficient submission- we are aiming to have the podcast up and functional within 7 days and may award the project alot earlier if the right eye catching design presents. We value creativity and your own influence on the design over our own percieved expectations.

We like the simplicity of the following templates - Steady Deck and Dune Crew

http://palmerthemes.net/shop/steady-music-themes/steady-deck/

http://templatebazaar.net/item/dunecrew-music-band-premium-wordpress-theme/7310452?WT.ac=category_item&WT.seg_1=category_item&WT.z_author=vexmark

The key is that we are chasing something that optimises list signups and social connectivity.
 

Target Market(s)

Gen Y- Young driven intelligent individuals, that seek out information and are or have aspirations to start their own businesses. Our target market loves to laugh.

Industry/Entity Type

Build

Requirements
Must have
• - Podcast Downloads
- Email sign up
- Affiliate Links with Thumbnail Preview
- Social Sharing and Connectivity
Nice to have
• - Sharing pictures/ youtube videos
Should not have
• Excessive amount of content that distract users from the objective of enjoying the podcast and signing up to our list.

```html
<!DOCTYPE html>
<html lang="en">
<head>
<meta charset="utf-8">
<title>Rowdy Ledgers with Tarq and Milo</title>
<link href="https://fonts.googleapis.com/css2?family=Roboto+Condensed:wght@400;700&family=Arimo:wght@400;700&display=swap" rel="stylesheet">
<style>
:root{
  --red:#d0161e;
  --red-bright:#e8141c;
  --red-dark:#9c0f15;
  --ink:#111111;
  --panel:#1e1e1e;
  --footer:#000000;
  --grey:#e4e4e4;
  --white:#ffffff;
  --text:#222222;
  --field:#e2e2e2;
}
*{margin:0;padding:0;box-sizing:border-box}
html,body{width:967px;height:1200px;overflow:hidden;background:var(--white)}
body{font-family:"Roboto Condensed",sans-serif;color:var(--text)}
.page{position:relative;width:967px;height:1200px;overflow:hidden}
.abs{position:absolute}

/* header */
.site-header{left:0;top:0;width:967px;height:48px;background:var(--white)}
.brand{left:106px;top:0;width:144px;height:98px;background:var(--white);z-index:5;display:flex;flex-direction:column;align-items:center;justify-content:center;gap:6px;padding:6px;text-align:center}
.brand-dot{width:20px;height:20px;border-radius:50%;background:var(--red)}
.brand-name{font-weight:700;font-size:13px;line-height:1.15;color:var(--ink);text-transform:uppercase}
.main-nav{left:310px;top:30px;display:flex;gap:13px;font-size:11.5px;font-weight:700;color:var(--ink)}
.main-nav .active{color:var(--red)}
.account-links{left:744px;top:4px;font-size:9.5px;font-weight:700;color:var(--ink)}
.call-us{left:716px;top:17px;font-size:17px;font-weight:700;color:var(--red)}

/* hero */
.hero{left:0;top:48px;width:967px;height:270px;background:linear-gradient(90deg,#1a1a1a 0%,#3a0a0c 25%,#c0141b 50%,#4a0c0e 75%,#141414 100%)}
.slider-dots{left:156px;top:282px;display:flex;gap:5px;align-items:center}
.slider-dots span{width:18px;height:18px;border-radius:50%;background:var(--white)}
.slider-dots .current{width:24px;height:24px;background:var(--red)}
.signin{left:672px;top:136px;width:178px;height:136px;background:var(--white);border:3px solid var(--red-dark);border-radius:5px;overflow:hidden}
.signin h2{background:linear-gradient(var(--red-bright),var(--red-dark));color:var(--white);font-size:17px;text-align:center;height:25px;line-height:25px;text-transform:uppercase}
.signin-row{display:flex;align-items:center;justify-content:space-between;padding:0 6px;height:23px;font-size:10px;font-weight:700}
.signin-row:first-of-type{margin-top:6px}
.signin-row i{display:block;width:98px;height:11px;background:var(--field)}
.signin-submit{display:block;margin:8px auto 0;width:56px;height:16px;background:var(--ink);color:var(--white);border-radius:3px;font-size:10px;font-weight:700;text-align:center;line-height:16px}

.band{left:0;width:967px;background:var(--red)}

/* features */
.features{left:0;top:325px;width:967px;height:153px;background:var(--panel)}
.feature{top:12px;width:200px;margin-left:-100px;text-align:center;color:var(--white)}
.feature svg{display:block;margin:0 auto;width:36px;height:36px}
.feature h3{font-size:19px;margin-top:10px;line-height:1}
.feature p{font-family:Arimo,sans-serif;font-size:10px;line-height:25px;margin-top:2px}
.btn-more{display:inline-block;width:64px;height:20px;line-height:20px;background:var(--red);color:var(--ink);font-weight:700;font-size:12px;margin-top:4px}

/* welcome */
.section-title{font-size:19px;font-weight:700;color:var(--red);text-transform:uppercase}
.welcome-text{left:106px;top:524px;width:432px;font-family:Arimo,sans-serif;font-size:9.8px;line-height:20.5px;color:var(--ink)}
.read-more{left:347px;top:641px;font-size:11px;font-weight:700;color:var(--red)}
.video{left:574px;top:524px;width:288px;height:132px;background:#ddd;border:1px solid #bbb}
.video-frame{position:absolute;left:0;top:0;width:286px;height:114px;background:linear-gradient(90deg,#d9d9d9,#8a8a8a 45%,#efefef)}
.video-play{position:absolute;left:122px;top:38px}
.video-bar{position:absolute;left:0;bottom:0;width:286px;height:16px;background:linear-gradient(#f4f4f4,#c8c8c8);display:flex;align-items:center;gap:5px;padding:0 4px;font-size:7px;font-family:Arimo,sans-serif}
.video-bar .track{flex:1;height:4px;background:#777;border-radius:2px}

/* popular */
.popular{left:0;top:679px;width:967px;height:151px;background:var(--grey)}
.thumb{top:34px;width:171px;height:113px}
.arrow-btn{top:64px;width:24px;height:24px}

/* social */
.collage{left:106px;top:853px;width:756px;height:195px;background:linear-gradient(90deg,#5a5a5a,#c9c9c9 30%,#7d7d7d 60%,#d4d4d4 85%,#666)}
.social-box{left:155px;top:895px;width:648px;height:108px;background:var(--red);color:var(--white);padding:22px 20px}
.social-box h2{font-size:19px;text-transform:uppercase}
.social-box p{font-size:10.5px;font-weight:700;margin-top:12px;text-transform:uppercase;color:var(--ink)}
.social-box p b{color:var(--white);margin-left:8px}

/* footer */
.site-footer{left:0;top:1064px;width:967px;height:136px;background:var(--footer);color:var(--white)}
.subscribe-title{left:138px;top:20px;font-size:16px;font-weight:700;text-transform:uppercase}
.subscribe-box{left:106px;top:46px;width:177px;height:54px;background:linear-gradient(#f2f2f2,#9a9a9a);padding:5px 6px;color:var(--ink)}
.subscribe-box p{font-size:9.5px;font-weight:700;text-align:center}
.subscribe-field{position:absolute;left:6px;top:29px;width:136px;height:15px;border-radius:8px;background:#e9e9e9;font-family:Arimo,sans-serif;font-size:7.5px;color:#999;text-align:center;line-height:15px}
.subscribe-go{position:absolute;left:148px;top:24px;width:23px;height:23px;border-radius:50%;background:#1a1a1a;color:var(--white);font-size:9px;font-weight:700;line-height:23px;text-align:center}
.footer-nav{left:325px;top:74px;display:flex;gap:9px;font-size:9.5px;font-weight:700;text-transform:uppercase}
.copyright{left:376px;top:94px;font-size:7.5px;font-weight:700;text-transform:uppercase}
.footer-social{left:686px;top:24px;display:flex;gap:12px}
.footer-social span{width:20px;height:20px;border-radius:50%;background:var(--white)}
.footer-brand{left:686px;top:56px;width:120px;text-align:center;font-size:11px;font-weight:700;text-transform:uppercase;line-height:1.2}
</style>
</head>
<body>
<div class="page">

  <header class="site-header abs"></header>
  <div class="brand abs">
    <span class="brand-dot"></span>
    <span class="brand-name">Rowdy Ledgers with Tarq and Milo</span>
  </div>
  <nav class="main-nav abs">
    <span class="active">HOME</span><span>ABOUT US</span><span>PODCAST</span><span>CALENDAR</span><span>FEATURES</span><span>BLOG</span><span>CONTACT US</span>
  </nav>
  <div class="account-links abs">SIGN UP &nbsp;|&nbsp; LOG IN</div>
  <div class="call-us abs">CALL US: 333-555-010</div>

  <section class="hero abs" role="img" aria-label="Photo of the hosts and guests recording a podcast around a studio table, tinted red"></section>
  <div class="slider-dots abs"><span class="current"></span><span></span><span></span><span></span><span></span></div>

  <form class="signin abs">
    <h2>Sign-in Form</h2>
    <div class="signin-row">EMAIL:<i></i></div>
    <div class="signin-row">FIRST NAME:<i></i></div>
    <div class="signin-row">LAST NAME:<i></i></div>
    <span class="signin-submit">SUBMIT</span>
  </form>

  <div class="band abs" style="top:318px;height:7px"></div>

  <section class="features abs">
    <div class="feature abs" style="left:174px">
      <svg viewBox="0 0 36 36"><rect width="36" height="36" rx="3" fill="#fff"/><circle cx="24" cy="10" r="4" fill="#1e1e1e"/><circle cx="12" cy="18" r="4" fill="#1e1e1e"/><circle cx="24" cy="26" r="4" fill="#1e1e1e"/><path d="M12 18 24 10M12 18 24 26" stroke="#1e1e1e" stroke-width="2"/></svg>
      <h3>Share</h3>
      <p>"Lorem Ipsum is simply dummy<br>text of the printing and typesetting</p>
      <span class="btn-more">MORE</span>
    </div>
    <div class="feature abs" style="left:370px">
      <svg viewBox="0 0 36 36"><rect x="2" y="4" width="30" height="30" fill="none" stroke="#fff" stroke-width="3"/><path d="M8 18 16 26 34 4" fill="none" stroke="#fff" stroke-width="5"/></svg>
      <h3>Publish</h3>
      <p>"Lorem Ipsum is simply dummy<br>text of the printing and typesetting</p>
      <span class="btn-more">MORE</span>
    </div>
    <div class="feature abs" style="left:595px">
      <svg viewBox="0 0 36 36"><text x="18" y="14" font-family="Arimo,sans-serif" font-weight="700" font-size="15" fill="#fff" text-anchor="middle">$</text><path d="M2 24h8l8 3 12-6 3 2-14 9-9-3H2z" fill="#fff"/></svg>
      <h3>Earn</h3>
      <p>"Lorem Ipsum is simply dummy<br>text of the printing and typesetting</p>
      <span class="btn-more">MORE</span>
    </div>
    <div class="feature abs" style="left:793px">
      <svg viewBox="0 0 36 36"><rect width="36" height="36" rx="3" fill="#fff"/><path d="M15 6h6v12h6l-9 9-9-9h6z" fill="#1e1e1e"/><rect x="7" y="29" width="22" height="3" fill="#1e1e1e"/></svg>
      <h3>Downloads</h3>
      <p>"Lorem Ipsum is simply dummy<br>text of the printing and typesetting</p>
      <span class="btn-more">MORE</span>
    </div>
  </section>

  <div class="band abs" style="top:478px;height:7px"></div>

  <h2 class="section-title abs" style="left:133px;top:494px">Welcome ,</h2>
  <p class="welcome-text abs">Lorem Ipsum is simply dummy text of the printing and typesetting industry. Lorem Ipsum has been the industry's standard dummy text ever since the 1500s, when an unknown printer took a galley of type and scrambled it to make a type specimen book. It has survived not only five centuries, but also the leap into electronic typesetting, remaining essentially unchanged. It was popularised in the 1960s with the release of Letraset sheets containing Lorem Ipsum passages, and more recently with desktop publishing software like Aldus PageMaker including versions of Lorem Ipsum.</p>
  <span class="read-more abs">MORE...</span>

  <h2 class="section-title abs" style="left:665px;top:494px">Watch Vedio</h2>
  <div class="video abs">
    <div class="video-frame" role="img" aria-label="Video still of a speaker presenting to an audience"></div>
    <svg class="video-play" width="46" height="46" viewBox="0 0 46 46"><circle cx="23" cy="23" r="21" fill="#333" stroke="#fff" stroke-width="3"/><path d="M18 13 33 23 18 33z" fill="#fff"/></svg>
    <div class="video-bar"><span>&#10074;&#10074;</span><span class="track"></span><span>0:00 / 6:66</span><span>&#9632;</span><span>&#9632;</span></div>
  </div>

  <div class="band abs" style="top:670px;height:9px"></div>

  <section class="popular abs">
    <h2 class="section-title abs" style="left:133px;top:6px">Popular,</h2>
    <svg class="arrow-btn abs" style="left:108px" viewBox="0 0 24 24"><circle cx="12" cy="12" r="11" fill="#fff" stroke="#999"/><path d="M14 7 9 12 14 17" fill="none" stroke="#222" stroke-width="2.5"/></svg>
    <div class="thumb abs" style="left:134px;background:linear-gradient(135deg,#2d3a55,#8a8f9a)" role="img" aria-label="Thumbnail of a surprised guest in a studio"></div>
    <div class="thumb abs" style="left:310px;background:linear-gradient(135deg,#7a1a1a,#3a3a3a)" role="img" aria-label="Thumbnail of a television panel discussion"></div>
    <div class="thumb abs" style="left:485px;background:linear-gradient(135deg,#2a2a4a,#6a3a5a)" role="img" aria-label="Thumbnail of people at a networking event"></div>
    <div class="thumb abs" style="left:661px;background:linear-gradient(135deg,#b8b0a4,#4a4a4a)" role="img" aria-label="Thumbnail of a conference talk"></div>
    <svg class="arrow-btn abs" style="left:835px" viewBox="0 0 24 24"><circle cx="12" cy="12" r="11" fill="#fff" stroke="#999"/><path d="M10 7 15 12 10 17" fill="none" stroke="#222" stroke-width="2.5"/></svg>
  </section>

  <div class="band abs" style="top:830px;height:10px"></div>

  <div class="collage abs" role="img" aria-label="Black and white mosaic of community member portraits"></div>
  <div class="social-box abs">
    <h2>Get Social Sharing and Connectivity</h2>
    <p>Want to know more about how it happen, or start your own?<b>Learn More</b></p>
  </div>

  <footer class="site-footer abs">
    <div class="subscribe-title abs">Subscribe Today!</div>
    <div class="subscribe-box abs">
      <p>Sign up to our program and promote ...</p>
      <span class="subscribe-field">YOUR EMAIL HERE</span>
      <span class="subscribe-go">GO</span>
    </div>
    <nav class="footer-nav abs"><span>Home</span><span>About Us</span><span>Podcast</span><span>Calendar</span><span>Features</span><span>Blog</span><span>Contact Us</span></nav>
    <div class="copyright abs">Copy-rights@Rowdy Ledgers with Tarq and Milo</div>
    <div class="footer-social abs"><span></span><span></span><span></span><span></span></div>
    <div class="footer-brand abs">Rowdy Ledgers with Tarq and Milo</div>
  </footer>

</div>
</body>
</html>
```